MRT Property - Business Cards

Looking for a business card & general letterhead, signage etc design for our new logo.

Colours:
000a20
0056a2
00b5ef
0088ce
68cef2

Fonts:
Poppins
Karla

Please keep look and feel of new brand - example in the zip package I sent.

```html
<!DOCTYPE html>
<html lang="en">
<head>
<meta charset="utf-8">
<title>MRT Property – Business Card</title>
<link rel="stylesheet" href="https://fonts.googleapis.com/css2?family=Montserrat:wght@300;400;700;800&family=Gochi+Hand&display=swap">
<style>
  :root {
    --page: #9b9b9b;
    --front-bg: #121527;
    --navy-deep: #000a20;
    --brand-blue: #0d56a6;
    --brand-mid: #0088ce;
    --brand-cyan: #00b5ef;
    --brand-light: #68cef2;
    --name-blue: #2a8fcf;
    --text-light: #f2f4f8;
    --icon-blue: #2b7fc8;
  }
  * { box-sizing: border-box; margin: 0; padding: 0; }
  html, body {
    width: 1093px; height: 1200px; overflow: hidden;
    background: var(--page);
    font-family: "Montserrat", Arial, sans-serif;
  }
  .canvas { position: relative; width: 1093px; height: 1200px; }
  .card {
    position: absolute; left: 265px; width: 580px; height: 363px;
    border-radius: 20px; overflow: hidden;
  }
  .card--front { top: 225px; background: var(--front-bg); }
  .card--back { top: 616px; height: 366px; background: var(--brand-blue); }

  .wordmark { position: absolute; color: #fff; font-weight: 800; }
  .wordmark__name { display: block; font-size: 78px; line-height: 1; letter-spacing: -2px; }
  .wordmark__sub { display: block; font-size: 19px; letter-spacing: 11px; margin-top: 10px; padding-left: 6px; }
  .card--front .wordmark { left: 27px; top: 28px; }

  .person { position: absolute; right: 33px; top: 24px; text-align: right; }
  .person__name { font-family: "Gochi Hand", cursive; color: var(--name-blue); font-size: 29px; line-height: 1.1; }
  .person__role { color: var(--text-light); font-size: 13px; font-weight: 400; letter-spacing: 0.3px; margin-top: 2px; }
  .person-tab { position: absolute; right: 0; top: 27px; width: 14px; height: 41px; background: var(--brand-blue); }

  .address { position: absolute; left: 31px; top: 199px; color: var(--text-light); font-size: 14px; font-weight: 300; line-height: 1.2; }
  .contact { position: absolute; left: 31px; top: 268px; list-style: none; }
  .contact li { display: flex; align-items: center; height: 24px; color: var(--text-light); font-size: 13.5px; font-weight: 400; }
  .contact svg { width: 14px; height: 14px; margin-right: 8px; fill: var(--icon-blue); flex: none; }

  .feature-art {
    position: absolute; left: 318px; top: 125px; width: 240px; height: 223px;
    border-radius: 60% 40% 0 70% / 40% 30% 0 80%;
    background: radial-gradient(circle at 70% 25%, #2c3358 0%, #161a30 40%, #07080f 85%);
  }
  .base-band { position: absolute; left: 0; bottom: 0; width: 100%; height: 15px; background: var(--brand-blue); }

  .pattern-field {
    position: absolute; inset: 0;
    background: linear-gradient(125deg, var(--brand-cyan) 0%, #2178b8 25%, #1e4f9c 55%, #1c3f86 100%);
    opacity: 0.55;
  }
  .card--back .wordmark { left: 393px; top: 267px; }
  .card--back .wordmark__name { font-size: 34px; letter-spacing: -0.5px; }
  .card--back .wordmark__sub { font-size: 8px; letter-spacing: 4.5px; margin-top: 2px; padding-left: 3px; }
  .brand-dot { position: absolute; left: 352px; top: 272px; width: 32px; height: 32px; border-radius: 50%; background: var(--brand-light); }
</style>
</head>
<body>
<main class="canvas">
  <section class="card card--front">
    <div class="wordmark">
      <span class="wordmark__name">MRT</span>
      <span class="wordmark__sub">PROPERTY</span>
    </div>

    <div class="person">
      <p class="person__name">Dana Whitfield</p>
      <p class="person__role">Managing Director</p>
    </div>
    <div class="person-tab"></div>

    <div class="feature-art" role="img" aria-label="Large dark decorative brand shape"></div>

    <p class="address">240 Harbor Ridge Road<br>Clinton, MS 39056</p>

    <ul class="contact">
      <li>
        <svg viewBox="0 0 24 24" aria-hidden="true"><path d="M6.6 10.8a15 15 0 0 0 6.6 6.6l2.2-2.2a1 1 0 0 1 1-.25 11.4 11.4 0 0 0 3.6.57 1 1 0 0 1 1 1V20a1 1 0 0 1-1 1A17 17 0 0 1 3 4a1 1 0 0 1 1-1h3.5a1 1 0 0 1 1 1c0 1.25.2 2.45.57 3.57a1 1 0 0 1-.25 1z"/></svg>
        555.014.2290
      </li>
      <li>
        <svg viewBox="0 0 24 24" aria-hidden="true"><path d="M2 5h20v14H2z M2 5l10 7 10-7" /></svg>
        info@mrtproperty.com
      </li>
      <li>
        <svg viewBox="0 0 24 24" aria-hidden="true"><circle cx="12" cy="12" r="10"/></svg>
        www.mrtproperty.com
      </li>
    </ul>

    <div class="base-band"></div>
  </section>

  <section class="card card--back">
    <div class="pattern-field" role="img" aria-label="Repeating decorative brand pattern fading from cyan to deep blue"></div>
    <span class="brand-dot"></span>
    <div class="wordmark">
      <span class="wordmark__name">MRT</span>
      <span class="wordmark__sub">PROPERTY</span>
    </div>
  </section>
</main>
</body>
</html>
```